Lo Mara Menu Design Project

This project is pretty straight forward. You will be given 3 files which include the following:
1. Our proposed menu
2. Our Company logo
3. A sample menu on what we are looking for design wise

Your job is to create a visually pleasing menu that is simple, clean and fresh. Please refer to our home website for additional information. (www.lomara-eats.com) Must be in eps or equivalent format.

Target Market(s)

20s to 40s

Industry/Entity Type

It Company

Requirements
Must have
• Company log
Must be in EPS format

```html
<!DOCTYPE html>
<html lang="en">
<head>
<meta charset="utf-8">
<title>Lo Mara Menu – Noodles, Tea &amp; Beverages</title>
<link href="https://fonts.googleapis.com/css2?family=Comfortaa:wght@700&family=Julius+Sans+One&family=Raleway:ital,wght@1,300&display=swap" rel="stylesheet">
<style>
  :root {
    --ink: #000000;
    --text: #ffffff;
    --accent: #c8202c;
    --gold: #c9a437;
    --red-deep: #5a1114;
  }
  * { margin: 0; padding: 0; box-sizing: border-box; }
  html, body { width: 1200px; height: 1000px; overflow: hidden; background: var(--ink); }
  .menu {
    position: relative; width: 1200px; height: 1000px; overflow: hidden;
    background: var(--ink); color: var(--text);
  }
  .pattern { position: absolute; inset: 0; width: 1200px; height: 1000px; }
  .rule { position: absolute; background: var(--accent); }
  .rule--vertical { left: 600px; top: 35px; width: 3px; height: 640px; }
  .rule--horizontal { left: 40px; top: 675px; width: 1112px; height: 3px; }
  .section-title {
    position: absolute; font-family: "Julius Sans One", sans-serif;
    color: var(--accent); font-size: 24px; line-height: 30px;
    text-align: center; letter-spacing: 0.5px; font-weight: 400;
  }
  .section-title--noodles { left: 53px; width: 487px; top: 36px; }
  .section-title--tea { left: 660px; width: 490px; top: 36px; }
  .section-title--beverages { left: 400px; width: 400px; top: 688px; }
  .item-list { position: absolute; }
  .item-list--noodles { left: 53px; top: 78px; width: 487px; }
  .item-list--tea { left: 667px; top: 78px; width: 483px; }
  .item-head {
    display: flex; justify-content: space-between;
    font-family: "Comfortaa", sans-serif; font-weight: 700;
    font-size: 17px; line-height: 21px; white-space: nowrap;
  }
  .item-desc {
    font-family: "Raleway", sans-serif; font-style: italic; font-weight: 300;
    font-size: 18.5px; letter-spacing: 0.3px; line-height: 20.7px;
    text-align: right; white-space: nowrap;
  }
  .bev-col { position: absolute; top: 742px; }
  .bev-col--left { left: 53px; width: 495px; }
  .bev-col--right { left: 660px; width: 490px; }
  .bev-item { margin-bottom: 20px; }
  .bev-item--tight { margin-bottom: 0; }
  .bev-size {
    display: flex; justify-content: space-between;
    font-family: "Raleway", sans-serif; font-style: italic; font-weight: 300;
    font-size: 18.5px; letter-spacing: 0.3px; line-height: 21px;
  }
  .brand-mark {
    position: absolute; display: flex; align-items: center; gap: 5px;
    font-family: "Comfortaa", sans-serif; font-weight: 700;
    font-size: 15px; color: var(--accent);
  }
  .brand-mark__square { width: 11px; height: 11px; background: var(--accent); }
  .brand-mark--left { left: 6px; top: 932px; }
  .brand-mark--right { left: 1116px; top: 932px; }
</style>
</head>
<body>
<main class="menu">
  <svg class="pattern" role="img" aria-label="Decorative pattern of large swirl circles in gold across the top and deep red across the bottom" viewBox="0 0 1200 1000">
    <defs>
      <linearGradient id="patternTone" x1="0" y1="0" x2="0" y2="1">
        <stop offset="0" stop-color="#6b5417" stop-opacity="0.55"/>
        <stop offset="0.3" stop-color="#2a200a" stop-opacity="0.3"/>
        <stop offset="0.55" stop-color="#000000" stop-opacity="0"/>
        <stop offset="0.8" stop-color="#3a0b0d" stop-opacity="0.45"/>
        <stop offset="1" stop-color="#7a1519" stop-opacity="0.7"/>
      </linearGradient>
    </defs>
    <rect width="1200" height="1000" fill="url(#patternTone)"/>
  </svg>

  <div class="rule rule--vertical"></div>
  <div class="rule rule--horizontal"></div>

  <h2 class="section-title section-title--noodles">NOODLES</h2>
  <section class="item-list item-list--noodles">
    <div class="item-head"><span>Lo Mein</span><span>10.95</span></div>
    <p class="item-desc">Soft lo mein noodles with shredded vegetables and<br>chicken, pork, or vegetables.<br>Beef or shrimp instead, add $1.00.</p>
    <div class="item-head"><span>Chow Mein</span><span>12.95</span></div>
    <p class="item-desc">Crispy egg noodles or soft lo mein noodles with large<br>vegetables and chicken, pork, or vegetables.<br>Beef or shrimp instead, add $1.00.</p>
    <div class="item-head"><span>Pad Thai</span><span>12.95</span></div>
    <p class="item-desc">Rice noodles with chicken, shrimp, eggs, onions, and<br>scallions topped with peanuts and cilantro.</p>
    <div class="item-head"><span>Peanut Noodles</span><span>8.95</span></div>
    <p class="item-desc">Soft lo mein noodles with scallions, chopped peanuts,<br>preserved szechwan vegetables, and a spicy peanut<br>sauce.<br>Add chicken $2.00.</p>
    <div class="item-head"><span>Tavi's Noodles</span><span>9.95</span></div>
    <p class="item-desc">Lo mein noodles with sliced chicken breast in a spicy<br>cilantro sauce.</p>
    <div class="item-head"><span>Singapore Noodles</span><span>10.95</span></div>
    <p class="item-desc">Shrimp, barbeque pork, bean sprouts, onions, egg, and<br>bell peppers with rice noodles in a curry sauce.</p>
    <div class="item-head"><span>Chow Fun</span><span>10.95</span></div>
    <p class="item-desc">Chicken, pork, or vegetables with bean sprouts, scallions,<br>onions, and wide rice noodles. For beef or shrimp in-<br>stead, add $1.00.</p>
  </section>

  <h2 class="section-title section-title--tea">LEAF &amp; KETTLE BY THE POT</h2>
  <section class="item-list item-list--tea">
    <div class="item-head"><span>Green Kukicha Tea</span><span>3.75</span></div>
    <p class="item-desc">Often enjoyed for its health benefits, this tea has a fresh<br>green, grassy taste with a crisp finish.</p>
    <div class="item-head"><span>Ginger Ginseng Tea</span><span>3.75</span></div>
    <p class="item-desc">This unique chamomile blend is velvety, yet mellow with a<br>complex finish of cinnamon, apple, and lime. Caffeine-<br>Free.</p>
    <div class="item-head"><span>White Coconut Crème</span><span>3.75</span></div>
    <p class="item-desc">Tender white peony leaves blended with cornflower, saf-<br>flower, and sweet creamy coconut.</p>
    <div class="item-head"><span>Wuyi Oolong Tea</span><span>3.75</span></div>
    <p class="item-desc">Long beautiful leaves unwind and unfurl when steeped<br>to release a smooth, rice flavor with crisp and earthy<br>tones.</p>
    <div class="item-head"><span>Premium Halo Tea</span><span>4.25</span></div>
    <p class="item-desc">Hand-Tied white tea blossoms into a rainbow of jasmine<br>and amaranth flowers with fresh fruit notes.</p>
    <div class="item-head"><span>Fjora Water</span><span>0.00</span></div>
    <p class="item-desc">Sparkling or flat. Small 375 ml $4.00.Large 800 ml $6.00.</p>
    <div class="item-head"><span>Jasmine Reserve Tea</span><span>3.75</span></div>
    <p class="item-desc">Organic fair trade green tea repeatedly baked and<br>scented with fresh and fragrant jasmine blossoms.</p>
    <div class="item-head"><span>English Breakfast Tea</span><span>3.75</span></div>
    <p class="item-desc">A smooth malty brew with a clean finish, this is our<br>house's traditional blend of organic black tea.</p>
    <div class="item-head"><span>Chamomile Clementine Tea</span><span>3.75</span></div>
    <p class="item-desc">This unique chamomile blend is velvety, yet mellow with a<br>complex finish of cinnamon, apple, and lime. Caffeine-</p>
  </section>

  <h2 class="section-title section-title--beverages">BEVERAGES</h2>
  <section class="bev-col bev-col--left">
    <div class="bev-item">
      <div class="item-head"><span>FJORA (Sparkling or Still)</span></div>
      <div class="bev-size"><span>Small (375ml</span><span>4.00</span></div>
      <div class="bev-size"><span>Large (800ml)</span><span>6.50</span></div>
    </div>
    <div class="bev-item bev-item--tight">
      <div class="item-head"><span>Cola</span><span>2.75</span></div>
      <p class="item-desc">Cola, Diet Cola, Lime Soda, Cherry Cola, Orange Soda</p>
      <div class="item-head"><span>Lemonade</span><span>3.50</span></div>
    </div>
  </section>
  <section class="bev-col bev-col--right">
    <div class="bev-item">
      <div class="item-head"><span>Orange &amp; Cranberry Juice</span><span>3.50</span></div>
    </div>
    <div class="bev-item">
      <div class="item-head"><span>Iron Ridge French Press Coffee</span><span>3.95</span></div>
      <p class="item-desc">Caffeinated or Decaffeinated</p>
    </div>
    <div class="bev-item">
      <div class="item-head"><span>Iced Teas</span><span>2.75</span></div>
      <p class="item-desc">Traditional, Mango, Blackberry Jasmine Green</p>
    </div>
  </section>

  <div class="brand-mark brand-mark--left"><span class="brand-mark__square"></span><span>Lo Mara</span></div>
  <div class="brand-mark brand-mark--right"><span class="brand-mark__square"></span><span>Lo Mara</span></div>
</main>
</body>
</html>
```